Birchline Septic Solutions

Would like to see some single sided ones but would also like to see some double sided with one sided only being the logo. Owners name is Colin Vandro. Phone number is 555-214-0387
Services are pumping, inspections, installs, and repairs

Contact Information for Business Card

555-241-0387 Colin Vandro Fernbrook, OH

```html
<!DOCTYPE html>
<html lang="en">
<head>
<meta charset="utf-8">
<title>Birchline Septic Solutions — Business Card</title>
<link href="https://fonts.googleapis.com/css2?family=Montserrat:wght@500;700;800&family=Open+Sans:wght@400;600&display=swap" rel="stylesheet">
<style>
  :root {
    --canvas-bg: #232323;
    --card-bg: #202024;
    --card-shade: #1a1a1d;
    --card-shade-deep: #161618;
    --band-edge: #2a2a2e;
    --teal: #2bb8b0;
    --white: #ffffff;
    --soft-white: #e9e9ea;
  }
  * { box-sizing: border-box; margin: 0; padding: 0; }
  html, body { width: 1200px; height: 779px; overflow: hidden; background: var(--canvas-bg); }
  .canvas { position: relative; width: 1200px; height: 779px; background: var(--canvas-bg); }

  .card {
    position: absolute;
    top: 105px;
    width: 330px;
    height: 570px;
    border-radius: 26px;
    overflow: hidden;
    background: var(--card-bg);
    box-shadow: 0 18px 40px rgba(0,0,0,.55);
  }
  .card--back { left: 215px; }
  .card--front { left: 655px; }

  /* back side */
  .back-pattern {
    position: absolute; inset: 0;
    background: linear-gradient(125deg, #6a6a6c 0%, #3a3a3d 22%, #1b1b1d 48%, #151517 100%);
  }
  .back-wordmark {
    position: absolute; top: 42px; right: 34px;
    display: flex; align-items: center; gap: 8px;
    font-family: "Montserrat", sans-serif; font-weight: 800;
    font-size: 13px; letter-spacing: 1px; color: var(--white);
    text-transform: uppercase; line-height: 1.2; text-align: right;
  }
  .back-wordmark .dot { width: 10px; height: 10px; border-radius: 50%; background: var(--white); flex: none; }

  /* front side */
  .front-bands { position: absolute; inset: 0; width: 100%; height: 100%; }
  .front-wordmark {
    position: absolute; top: 88px; left: 0; right: 0;
    text-align: center;
    font-family: "Montserrat", sans-serif; font-weight: 800;
    color: var(--white); text-transform: uppercase;
    font-size: 22px; letter-spacing: 1px; line-height: 1.3;
  }
  .contact {
    position: absolute; top: 262px; left: 0; right: 0; text-align: center;
  }
  .contact__name {
    font-family: "Montserrat", sans-serif; font-weight: 700; font-size: 30px; letter-spacing: .3px;
  }
  .contact__first { color: var(--teal); }
  .contact__last { color: var(--white); }
  .contact__place {
    font-family: "Open Sans", sans-serif; font-size: 17px; color: var(--soft-white); margin-top: 2px;
  }
  .contact__icon { display: block; margin: 10px auto 4px; }
  .contact__phone {
    font-family: "Open Sans", sans-serif; font-size: 25px; color: var(--white); letter-spacing: .5px;
  }
  .services {
    position: absolute; top: 432px; left: 110px; text-align: center; width: 170px;
  }
  .services__pill {
    display: inline-block; background: var(--teal); color: var(--white);
    font-family: "Open Sans", sans-serif; font-weight: 600; font-size: 16px;
    padding: 3px 24px; border-radius: 50%; letter-spacing: .5px;
  }
  .services__arrow { display: block; margin: 0 auto 2px; }
  .services__list {
    list-style: none; font-family: "Open Sans", sans-serif; font-size: 16px;
    line-height: 1.3; color: var(--soft-white);
  }
</style>
</head>
<body>
<main class="canvas">

  <section class="card card--back" aria-label="Business card back">
    <div class="back-pattern" role="img" aria-label="Repeating mountain and pine tree motif pattern with a silver foil sheen fading to black"></div>
    <div class="back-wordmark">
      <span>Birchline<br>Septic Solutions</span>
      <span class="dot"></span>
    </div>
  </section>

  <section class="card card--front" aria-label="Business card front">
    <svg class="front-bands" viewBox="0 0 330 570" preserveAspectRatio="none" aria-hidden="true">
      <path d="M0 330 Q120 380 330 250 L330 570 L0 570 Z" fill="var(--card-shade)"/>
      <path d="M0 330 Q120 380 330 250" fill="none" stroke="var(--band-edge)" stroke-width="2"/>
      <path d="M60 570 Q150 440 330 395 L330 570 Z" fill="var(--card-shade-deep)"/>
      <path d="M60 570 Q150 440 330 395" fill="none" stroke="var(--band-edge)" stroke-width="2"/>
    </svg>

    <div class="front-wordmark">Birchline<br>Septic Solutions</div>

    <div class="contact">
      <p class="contact__name"><span class="contact__first">Colin</span> <span class="contact__last">Vandro</span></p>
      <p class="contact__place">Fernbrook, OH</p>
      <svg class="contact__icon" width="30" height="38" viewBox="0 0 30 38" aria-hidden="true">
        <circle cx="15" cy="13" r="12" fill="var(--teal)"/>
        <path d="M10 8.5c0 5 3.5 8.5 8.5 8.5l1.5-2-2.5-1.5-1 1c-1.5-.6-2.9-2-3.5-3.5l1-1-1.5-2.5z" fill="var(--white)"/>
        <line x1="15" y1="25" x2="15" y2="32" stroke="var(--teal)" stroke-width="2"/>
        <path d="M10 30 L15 37 L20 30 Z" fill="var(--teal)"/>
      </svg>
      <p class="contact__phone">555-241-0387</p>
    </div>

    <div class="services">
      <span class="services__pill">SERVICES</span>
      <svg class="services__arrow" width="14" height="12" viewBox="0 0 14 12" aria-hidden="true">
        <path d="M1 2 L7 11 L13 2 Z" fill="var(--teal)"/>
      </svg>
      <ul class="services__list">
        <li>Installs</li>
        <li>Pumping</li>
        <li>Inspections</li>
        <li>And Repairs</li>
      </ul>
    </div>
  </section>

</main>
</body>
</html>
```